Communication and Marketing agency needs a new presentation card

We are a group of communication and marketing agencies specialized in companies that are in the logistics and industrial sector. The head agency is TELVANO Grupo and the group consists of 4 agencies: TELVANO Media, TELVANO Digital, TELVANO Research and DifundeEnPantalla. We hace 4 offices in Spain (Madrid, Barcelona, Valencia and Murcia). We are looking for a clean and attractive design that transmits our experience, brand presence in the market and knowledge to those who receive the card.It has to maintain the colors of the logo that is attached.
Target Market(s)
logistics and industrial sector
Marketing department
Contact Information for Business Card
Clean and attractive design

```html
<!DOCTYPE html>
<html lang="es">
<head>
<meta charset="UTF-8">
<title>TELVANO Grupo – Tarjeta de presentación</title>
<link rel="stylesheet" href="https://fonts.googleapis.com/css2?family=Roboto:wght@400;500;700&display=swap">
<style>
  :root {
    --brand-red: #c4161c;
    --ink: #3a3a3a;
    --ink-soft: #6b6b6b;
    --rule-grey: #8a8a8a;
    --card: #ffffff;
    --backdrop: #e6e6e6;
    --map-tone: #cfcfcf;
  }
  * { box-sizing: border-box; margin: 0; padding: 0; }
  html, body { width: 1200px; height: 900px; overflow: hidden; }
  body {
    background: var(--backdrop);
    font-family: "Roboto", Arial, sans-serif;
    color: var(--ink);
    position: relative;
  }
  .card {
    position: absolute;
    left: 250px;
    width: 700px;
    height: 400px;
    background: var(--card);
    border-radius: 22px;
    box-shadow: 0 6px 22px rgba(0,0,0,.12);
    overflow: hidden;
  }
  .card--front { top: 40px; }
  .card--back { top: 470px; }

  /* front */
  .group-name {
    position: absolute; left: 60px; top: 62px;
    font-size: 40px; font-weight: 500; letter-spacing: 1px;
    color: var(--brand-red);
  }
  .divider { position: absolute; top: 208px; height: 2px; }
  .divider--grey { left: 40px; width: 330px; background: var(--rule-grey); }
  .divider--red { left: 370px; width: 290px; background: var(--brand-red); }

  .person { position: absolute; right: 40px; top: 140px; text-align: right; }
  .person__name { font-size: 28px; font-weight: 700; color: var(--brand-red); line-height: 1.1; }
  .person__role { font-size: 17px; font-weight: 500; color: var(--ink); margin-top: 4px; }

  .contact-list { position: absolute; left: 40px; top: 238px; list-style: none; }
  .contact-list li {
    display: flex; align-items: center; gap: 10px;
    font-size: 17px; line-height: 26px; color: var(--ink);
  }
  .contact-list svg { width: 13px; height: 13px; fill: var(--brand-red); flex: none; }

  .agencies {
    position: absolute; left: 380px; top: 240px; width: 290px;
    display: grid; grid-template-columns: 1fr 1fr; row-gap: 26px; column-gap: 16px;
  }
  .agency { font-size: 17px; font-weight: 500; line-height: 1.2; }
  .agency--red { color: var(--brand-red); }
  .agency--grey { color: var(--ink-soft); }

  /* back */
  .office-map {
    position: absolute; left: 200px; top: 36px; width: 300px; height: 240px;
    background: radial-gradient(ellipse at center, var(--map-tone) 0%, #e9e9e9 75%, var(--card) 100%);
    border-radius: 40px;
  }
  .office-list {
    position: absolute; left: 0; right: 0; bottom: 52px; text-align: center;
    font-size: 24px; font-weight: 500; color: var(--ink); letter-spacing: .5px;
  }
  .office-list .sep { color: var(--brand-red); margin: 0 8px; }
</style>
</head>
<body>

<section class="card card--front" aria-label="Anverso de la tarjeta">
  <div class="group-name">TELVANO Grupo</div>

  <div class="person">
    <p class="person__name">Andrés Quiroga</p>
    <p class="person__role">Director</p>
  </div>

  <div class="divider divider--grey"></div>
  <div class="divider divider--red"></div>

  <ul class="contact-list">
    <li><svg viewBox="0 0 24 24"><path d="M6.6 10.8a15.1 15.1 0 0 0 6.6 6.6l2.2-2.2c.3-.3.7-.4 1-.2 1.1.4 2.3.6 3.6.6.6 0 1 .4 1 1V20c0 .6-.4 1-1 1A17 17 0 0 1 3 4c0-.6.4-1 1-1h3.5c.6 0 1 .4 1 1 0 1.3.2 2.5.6 3.6.1.3 0 .7-.2 1z"/></svg>910 555 214</li>
    <li><svg viewBox="0 0 24 24"><path d="M7 1h10a2 2 0 0 1 2 2v18a2 2 0 0 1-2 2H7a2 2 0 0 1-2-2V3a2 2 0 0 1 2-2zm0 3v14h10V4z"/></svg>600 555 718</li>
    <li><svg viewBox="0 0 24 24"><path d="M2 5h20v14H2zm2 2v.5l8 5 8-5V7l-8 5z"/></svg>aquiroga@telvano.es</li>
    <li><svg viewBox="0 0 24 24"><circle cx="12" cy="12" r="10"/></svg>www.telvano.es</li>
    <li><svg viewBox="0 0 24 24"><rect x="2" y="2" width="20" height="20" rx="3"/></svg>andresquiroga</li>
  </ul>

  <div class="agencies">
    <span class="agency agency--red">TELVANO Media</span>
    <span class="agency agency--grey">TELVANO Research</span>
    <span class="agency agency--grey">TELVANO Digital</span>
    <span class="agency agency--red">DifundeEnPantalla</span>
  </div>
</section>

<section class="card card--back" aria-label="Reverso de la tarjeta">
  <div class="office-map" role="img" aria-label="Mapa punteado de España con marcadores en Madrid, Barcelona, Valencia y Murcia"></div>
  <p class="office-list">Madrid<span class="sep">/</span>Barcelona<span class="sep">/</span>Valencia<span class="sep">/</span>Murcia</p>
</section>

</body>
</html>
```